Harvest Gateway Fellowship Ministries needs a fresh new web design

We are an up and coming multicultural church that aims to bring people into a life changing encounter with God. We need a fresh and inviting website in order to increase our internet presence and make us easier to connect with.
Here are some of the basic requirements for the site:
• Clearly displayed address, service times, and contact info
• A staff profile page
• An area for a calendar with upcoming events and their details
• Social media buttons
• Group pages for the different ministries (youth, children’s church, men, etc…)
• An area for donations and eCommerce
• A resources page for assorted media (podcasts, sermons, videos, etc.…)
• An area for prayer requests.

```html
<!DOCTYPE html>
<html lang="en">
<head>
<meta charset="utf-8">
<title>Harvest Gateway Fellowship Ministries</title>
<link rel="stylesheet" href="https://fonts.googleapis.com/css2?family=Varela+Round&display=swap">
<style>
:root{
  --blue:#1d5b8c;
  --ink:#222;
  --yellow:#fbdb7c;
  --yellow-deep:#f5c860;
  --orange:#d9661c;
  --panel:#e4e4e4;
  --footer:#ececec;
  --cal-dark:#3a3a3a;
}
*{margin:0;padding:0;box-sizing:border-box}
html,body{width:867px;height:1200px;overflow:hidden;background:#fff}
body{position:relative;font-family:"Varela Round",Arial,sans-serif;color:var(--ink)}
.abs{position:absolute}
.topline{left:0;top:0;width:867px;height:3px;background:var(--yellow)}
.brand{left:88px;top:40px;width:150px;display:flex;flex-direction:column;align-items:center;gap:8px}
.brand-mark{width:46px;height:46px;border-radius:50%;background:var(--yellow-deep)}
.brand-name{font-size:10px;color:var(--blue);text-align:center;line-height:1.3}
.contact-block{top:22px;font-size:9.5px;line-height:11.5px;color:var(--blue);text-align:right}
.address{right:275px}
.contact-info{right:121px}
.contact-divider{left:607px;top:14px;width:1px;height:56px;background:#e2e2e2}
.nav{left:342px;top:94px;width:444px;height:35px;background:var(--yellow);border-radius:0 4px 4px 0;clip-path:polygon(0 0,100% 0,100% 100%,0 100%,26px 50%)}
.nav a{position:absolute;top:10px;font-size:11.5px;color:var(--blue);text-decoration:none;transform:translateX(-50%);white-space:nowrap}
.band{left:0;top:142px;width:867px;height:12px;background:var(--yellow)}
.hero{left:0;top:154px;width:867px;height:339px;background:linear-gradient(180deg,#c07a84 0%,#e8a08c 35%,#e6a98a 55%,#7a5a5a 80%,#0c0c0c 100%)}
.hero-title{left:151px;top:240px;font-size:24px;color:var(--blue)}
.hero-verse{left:153px;top:274px;font-size:14.5px;line-height:17.5px;color:var(--blue)}
.hero-ref{left:280px;top:321px;font-size:12.5px;color:#111}
.dots{left:160px;top:453px;display:flex;gap:5px}
.dots span{width:11px;height:11px;border:2px solid #fff;border-radius:50%}
h2{position:absolute;font-weight:400;font-size:18px;color:var(--blue)}
.welcome-text{left:94px;top:530px;width:392px;font-size:9px;line-height:13px}
.welcome-text p+p{margin-top:13px}
.btn{position:absolute;background:var(--yellow);color:var(--blue);border-radius:4px;font-size:11px;display:flex;align-items:center;justify-content:center}
.staff-photo{left:518px;top:530px;width:104px;height:125px;background:linear-gradient(160deg,#7a5a4a,#3a2420 60%,#8a4a7a)}
.staff-caption{left:518px;top:634px;width:104px;height:21px;background:#111;color:#fff;font-size:9px;display:flex;align-items:center;justify-content:center}
.staff-details{left:630px;top:533px;font-size:10px;line-height:17.5px}
.staff-details .small{font-size:9px}
.event{left:94px;display:flex;gap:9px}
.date{width:45px;height:46px;background:var(--yellow-deep);border-radius:3px;text-align:center;color:#222;font-size:8.5px;line-height:9px;padding-top:4px}
.date b{display:block;font-weight:400;font-size:17px;line-height:18px}
.event p{width:175px;font-size:9px;line-height:17.5px;margin-top:-3px}
.calendar{left:334px;top:702px;width:152px;background:#ccc;border:1px solid #bbb;box-shadow:0 1px 2px rgba(0,0,0,.2)}
.cal-head{height:24px;background:var(--cal-dark);color:#fff;font-size:10px;display:flex;align-items:center;justify-content:space-between;padding:0 8px}
.cal-days,.cal-grid{display:grid;grid-template-columns:repeat(7,1fr)}
.cal-days{background:#eee;font-size:6px;color:#666;text-align:center;height:13px;line-height:13px}
.cal-grid span{height:21.5px;display:flex;align-items:center;justify-content:center;font-size:8.5px;color:#444;background:#ddd;border:1px solid #c9c9c9}
.cal-grid .muted{color:#aaa;background:#e9e9e9}
.cal-grid .today{background:var(--yellow-deep);color:var(--blue)}
.groups{left:516px;top:672px;width:270px;height:166px;background:linear-gradient(180deg,#fde08e,#f6c963);border-radius:3px}
.groups-title{position:absolute;left:14px;top:8px;font-size:18px;color:var(--blue)}
.groups-rule{position:absolute;left:10px;right:10px;top:32px;height:1px;background:#f3d27d}
.groups ul{position:absolute;left:14px;top:38px;list-style:none;font-size:13px;line-height:21.5px;color:#333}
.groups li{display:flex;align-items:center;gap:10px}
.donate-strip{position:absolute;left:0;right:0;top:116px;bottom:0;border-top:1px solid #f1c75c;background:#f6c55e;border-radius:0 0 3px 3px}
.donate-label{position:absolute;left:20px;top:12px;font-size:18px;color:var(--orange)}
.cards{position:absolute;left:118px;top:15px;display:flex;gap:6px}
.cards span{width:28px;height:18px;border-radius:2px;background:#fff;box-shadow:0 1px 1px rgba(0,0,0,.25)}
.cards span:nth-child(2){background:#e3713a}
.cards span:nth-child(4){background:#2d4f9c}
.tabs{left:90px;top:899px;width:400px;height:32px;background:#000;border-radius:4px 4px 0 0;display:flex;font-size:12px;color:#fff}
.tabs span{padding:0 8px;display:flex;align-items:center}
.tabs .active{background:var(--yellow);color:#222;border-radius:4px 0 0 0;padding:0 10px}
.media-body{left:90px;top:931px;width:400px;height:188px;background:#f7cd6e;border-radius:0 0 4px 4px;padding:10px 10px;font-size:8.8px;line-height:17.2px;letter-spacing:-0.1px}
.media-body p+p{margin-top:5px}
.prayer{left:513px;top:898px;width:270px;height:220px;background:var(--panel);border-radius:3px}
.prayer-photo{left:522px;top:910px;width:97px;height:103px;background:linear-gradient(150deg,#8a6a52,#3e2e26 60%,#6a5040);border-radius:2px}
.field{position:absolute;background:#fff;border-radius:3px;font-size:9.5px;color:#222;padding:0 10px;display:flex;align-items:center}
.field.message{align-items:flex-start;padding-top:8px}
.footer{left:0;top:1128px;width:867px;height:72px;background:var(--footer)}
.footer-nav{left:0;top:1152px;width:500px;height:14px}
.footer-nav a{position:absolute;top:0;font-size:9.5px;color:#333;text-decoration:none;white-space:nowrap}
.social{left:634px;top:1143px;display:flex;gap:15px}
.social span{width:22px;height:22px;border-radius:3px}
.copyright{right:105px;top:1179px;font-size:9px;color:#333}
</style>
</head>
<body>
<div class="abs topline"></div>

<div class="abs brand">
  <div class="brand-mark"></div>
  <div class="brand-name">Harvest Gateway Fellowship Ministries</div>
</div>

<div class="abs contact-block address">Addres : 01X Lorium ipsum<br>Sed usd huio,<br>City.</div>
<div class="abs contact-divider"></div>
<div class="abs contact-block contact-info">Contact Info<br>Email : info@harvestgateway.org<br>Phone : 555.010.4821</div>

<nav class="abs nav">
  <a style="left:55px">Home</a>
  <a style="left:116px">About Us</a>
  <a style="left:178px">Events</a>
  <a style="left:256px">Prayer Request</a>
  <a style="left:335px">Donate</a>
  <a style="left:404px">Contact Us</a>
</nav>
<div class="abs band"></div>

<section class="abs hero" role="img" aria-label="Sunset sky over grass with a kneeling figure in prayer, silhouetted"></section>
<div class="abs hero-title">Random Bible Verse</div>
<div class="abs hero-verse">Set your affection on things<br>above, not on things on the earth.</div>
<div class="abs hero-ref">Colossians 3:2</div>
<div class="abs dots"><span></span><span></span><span></span><span></span></div>

<h2 style="left:93px;top:500px">Welcome</h2>
<div class="abs welcome-text">
  <p>Welcome to Harvest Gateway Fellowship Ministries, a place where we can come together and fellowship. HGFM is located in Riverside Heights and we would love to have you worship with us. We believe God is doing something extraordinary through our church and would like for you to be a part. Please prayerfully consider our church as a place you would like to worship and fellowship with us as we continue to grow.</p>
  <p>As you venture on our website please feel free to contact us through email, phone, or leave a prayer request for us to pray on your behalf. Please take a minute and look at our upcoming events.</p>
</div>
<div class="btn" style="left:383px;top:650px;width:81px;height:21px">Read more</div>

<h2 style="left:518px;top:500px">A staff profile page</h2>
<div class="abs staff-photo" role="img" aria-label="Portrait of the ministry administrator in prayer"></div>
<div class="abs staff-caption">Read more About Me</div>
<div class="abs staff-details">
  Name : Marisol<br>Proffession : Ministry Aministrator<br>About :<br>
  <span class="small">Neque porro quisquam est qui<br>dolorem ipsum quia dolor sit amet,<br>consectetur, adipisci velit.<br>There is no one who loves pain</span>
</div>

<h2 style="left:93px;top:678px">Upcoming Events</h2>
<div class="abs event" style="top:715px">
  <div class="date">Mar<b>04</b>2011</div>
  <p>Neque porro quisquam est qui dolorem ipsum quia dolor sit amet, consectetur, adipisci velit.</p>
</div>
<div class="abs event" style="top:784px">
  <div class="date">Mar<b>04</b>2011</div>
  <p>Neque porro quisquam est qui dolorem ipsum quia dolor sit amet, consectetur, adipisci velit.</p>
</div>

<div class="abs calendar">
  <div class="cal-head"><span>◂</span><span>March 2011</span><span>▸</span></div>
  <div class="cal-days"><span>MON</span><span>TUE</span><span>WED</span><span>THU</span><span>FRI</span><span>SAT</span><span>SUN</span></div>
  <div class="cal-grid">
    <span class="muted">28</span><span>1</span><span>2</span><span>3</span><span class="today">4</span><span>5</span><span>6</span>
    <span>7</span><span>8</span><span>9</span><span>10</span><span>11</span><span>12</span><span>13</span>
    <span>14</span><span>15</span><span>16</span><span>17</span><span>18</span><span>19</span><span>20</span>
    <span>21</span><span>22</span><span>23</span><span>24</span><span>25</span><span>26</span><span>27</span>
    <span>28</span><span>29</span><span>30</span><span>31</span><span class="muted">1</span><span class="muted">2</span><span class="muted">3</span>
  </div>
</div>

<div class="abs groups">
  <div class="groups-title">Different Group Ministries</div>
  <div class="groups-rule"></div>
  <ul>
    <li><svg width="12" height="10" viewBox="0 0 12 10"><path d="M1 5l3.5 3.5L11 1.5" fill="none" stroke="#333" stroke-width="2.2"/></svg>Youth</li>
    <li><svg width="12" height="10" viewBox="0 0 12 10"><path d="M1 5l3.5 3.5L11 1.5" fill="none" stroke="#333" stroke-width="2.2"/></svg>Children’s church</li>
    <li><svg width="12" height="10" viewBox="0 0 12 10"><path d="M1 5l3.5 3.5L11 1.5" fill="none" stroke="#333" stroke-width="2.2"/></svg>Men</li>
  </ul>
  <div class="donate-strip">
    <div class="donate-label">Donate</div>
    <div class="cards"><span></span><span></span><span></span><span></span></div>
  </div>
</div>

<h2 style="left:94px;top:868px">Assorted media resources</h2>
<div class="abs tabs"><span class="active">Podcasts</span><span>Sermons</span><span>Videos</span></div>
<div class="abs media-body">
  <p>Neque porro quisquam est qui dolorem ipsum quia dolor sit amet, consectetur, adipisci velit.There is no one who loves pain&nbsp; Neque porro quisquam est, qui dolorem ipsum quia dolor sit amet, consectetur, adipisci velit, sed quia non numquam eius modi tempora incidunt ut labore et dolore magnam aliquam quaerat voluptatem. Ut enim ad minima veniam, quis nostrum exercitationem ullam corporis suscipit laboriosam</p>
  <p>Neque porro quisquam est qui dolorem ipsum quia dolor sit amet, consectetur, adipisci velit.There is no one who loves pain&nbsp; Neque porro quisquam est, qui dolorem ipsum quia dolor sit amet, consectetur, adipisci velit, sed quia non numquam eius modi tempora incidunt ut labore et dolore magnam aliquam</p>
</div>

<h2 style="left:522px;top:868px">Prayer Requests</h2>
<div class="abs prayer">
  <div class="field" style="left:113px;top:12px;width:147px;height:29px">Name</div>
  <div class="field" style="left:113px;top:49px;width:147px;height:29px">Phone</div>
  <div class="field" style="left:113px;top:86px;width:147px;height:29px">Email</div>
  <div class="field message" style="left:9px;top:125px;width:251px;height:59px">Message</div>
  <div class="btn" style="left:156px;top:190px;width:104px;height:22px">Submit a Request</div>
</div>
<div class="abs prayer-photo" role="img" aria-label="Couple praying together"></div>

<footer class="abs footer"></footer>
<nav class="abs footer-nav">
  <a style="left:89px">Home</a>
  <a style="left:134px">About Us</a>
  <a style="left:194px">Events</a>
  <a style="left:243px">Prayer Request</a>
  <a style="left:328px">Donate</a>
  <a style="left:380px">Contact</a>
</nav>
<div class="abs social">
  <span style="background:#f08a1c"></span>
  <span style="background:#3b5b9a"></span>
  <span style="background:#3fa6d0"></span>
  <span style="background:#c9302c"></span>
</div>
<div class="abs copyright">© 2014.www.harvestgateway.org</div>
</body>
</html>
```